Brookvale Estates LLC stationary for a real estate property management company.

Create stationary (letterhead, envelopes, business cards) using Brookvale Estates LLC logo as primary creative element. Stationary design needs to be horizontal, leaving as much space as possible for correspondence copy. See attached Creative Brief and past stationary files for details.

Target Market(s)

Prospective apartment residents and current residents, vendors, and government agencies.

Industry/Entity Type

Property Management

Contact Information for Business Card

Business card employee title: Property Manager. Should include address, phone, fax, email, website, slogan, and Brookvale Estates logo.

Font styles to use
Sans Serif

Colors
0592cd
000000

Requirements
Must have
• Tone should be conservative, institutional, business (i.e. banking, finance, real estate). Must include: address, phone, fax, website, and slogan (see attached Creative Brief). Should be a horizontal design, leaving as much room as possible for letter correspondence copy.
Nice to have
• Please use an Arial or Helvetica style font.
Should not have
• Letterhead layout should leave as much room as possible for copy.

```html
<!DOCTYPE html>
<html lang="en">
<head>
<meta charset="utf-8">
<title>Brookvale Estates LLC – Stationery</title>
<link href="https://fonts.googleapis.com/css2?family=Lato:wght@400;700&display=swap" rel="stylesheet">
<style>
  :root{
    --board:#c5bfad;
    --paper:#ffffff;
    --brand-blue:#1566a8;
    --ink:#2b2b2b;
    --charcoal:#474a4f;
    --faint-grey:#ececec;
    --shadow:rgba(0,0,0,.28);
  }
  *{box-sizing:border-box;margin:0;padding:0}
  html,body{width:1200px;height:1200px;overflow:hidden}
  body{background:var(--board);font-family:"Lato",Arial,sans-serif;color:var(--ink);position:relative}
  .sheet{position:absolute;background:var(--paper);box-shadow:2px 2px 3px var(--shadow);overflow:hidden}
  .abs{position:absolute}
  .wordmark{font-weight:700;color:var(--brand-blue);white-space:nowrap;display:flex;align-items:center;letter-spacing:.02em}
  .wordmark .dot{display:inline-block;border-radius:50%;background:var(--charcoal);margin-right:.4em;flex:none}
  .name{color:var(--brand-blue);font-size:13px}
  .name.dark{color:var(--ink)}
  .title{font-size:8.5px;color:var(--ink)}
  .contact{font-size:10.5px;line-height:12.5px}
  .contact li{list-style:none;display:flex;align-items:center;gap:4px}
  .contact .gap{margin-top:6px}
  .contact .addr{color:var(--brand-blue);margin-top:6px}
  .ico{width:10px;height:10px;flex:none}
  .small .ico{width:7px;height:7px}
  .card{width:318px;height:182px;top:179px}
  .card-front{left:70px}
  .card-alt{left:443px}
  .card-back{left:817px}
  .deco-ring{border-radius:50%}
  .pattern-field{position:absolute;inset:0;background:linear-gradient(135deg,#f7f7f7,#eeeeee)}
  .letterhead{left:70px;top:466px;width:482px;height:623px}
  .lh-contact{font-size:7px;line-height:9px}
  .envelope{left:602px;width:550px;height:245px}
  .env-front{top:466px}
  .env-back{top:758px}
  .flap{position:absolute;left:0;top:0;width:550px;height:84px}
</style>
</head>
<body>

<svg width="0" height="0" style="position:absolute" aria-hidden="true">
  <defs>
    <symbol id="i-phone" viewBox="0 0 10 10"><rect x=".5" y=".5" width="9" height="9" rx="1.5" fill="var(--brand-blue)"/><path d="M2.3 4.2c0-1.4 5.4-1.4 5.4 0v.6H6.3v-.6H3.7v.6H2.3zM2.8 5.5h4.4l.5 2.5H2.3z" fill="#fff"/></symbol>
    <symbol id="i-fax" viewBox="0 0 10 10"><rect x=".5" y=".5" width="9" height="9" rx="1.5" fill="var(--brand-blue)"/><rect x="3" y="2" width="4" height="2.2" fill="#fff"/><rect x="2" y="4.6" width="6" height="3.2" fill="#fff"/></symbol>
    <symbol id="i-mail" viewBox="0 0 10 10"><rect x=".5" y=".5" width="9" height="9" rx="1.5" fill="var(--brand-blue)"/><rect x="2" y="3" width="6" height="4" fill="#fff"/><path d="M2 3l3 2.4L8 3" stroke="var(--brand-blue)" stroke-width=".7" fill="none"/></symbol>
    <symbol id="i-web" viewBox="0 0 10 10"><rect x=".5" y=".5" width="9" height="9" rx="1.5" fill="var(--brand-blue)"/><circle cx="5" cy="5" r="3" fill="none" stroke="#fff" stroke-width=".8"/><path d="M2 5h6M5 2c-1.6 2-1.6 4 0 6M5 2c1.6 2 1.6 4 0 6" stroke="#fff" stroke-width=".6" fill="none"/></symbol>
    <symbol id="i-pin" viewBox="0 0 10 10"><rect x=".5" y=".5" width="9" height="9" rx="1.5" fill="var(--brand-blue)"/><path d="M5 8.3C3.3 6.3 2.8 5.4 2.8 4.3a2.2 2.2 0 0 1 4.4 0c0 1.1-.5 2-2.2 4z" fill="#fff"/><circle cx="5" cy="4.3" r=".8" fill="var(--brand-blue)"/></symbol>
  </defs>
</svg>

<section class="sheet card card-front" aria-label="Business card front">
  <div class="abs" style="left:25px;top:21px">
    <div class="name">Daniel Hayes</div>
    <div class="title">Property manager</div>
  </div>
  <ul class="abs contact" style="left:25px;top:82px">
    <li><svg class="ico"><use href="#i-phone"/></svg>555-014-2731</li>
    <li><svg class="ico"><use href="#i-fax"/></svg>555-014-2736</li>
    <li class="gap"><svg class="ico"><use href="#i-mail"/></svg>daniel@brookvaleestates.us</li>
    <li><svg class="ico"><use href="#i-web"/></svg>www.brookvaleestates.us</li>
    <li class="addr">2180 Larkin Ave. #310</li>
    <li style="color:var(--brand-blue)">Fairview, CA 90000</li>
  </ul>
  <div class="abs deco-ring" style="left:203px;top:58px;width:150px;height:150px;border:5px solid var(--charcoal)"></div>
</section>

<section class="sheet card card-alt" aria-label="Business card alternate">
  <div class="abs wordmark" style="left:18px;top:99px;font-size:9.5px">
    <span class="dot" style="width:13px;height:13px"></span>BROOKVALE ESTATES
  </div>
  <div class="abs" style="left:162px;top:26px">
    <div class="name dark" style="font-size:12px">Daniel Hayes</div>
    <div class="title" style="font-size:9.5px;margin-top:3px">Property manager</div>
  </div>
  <ul class="abs contact" style="left:162px;top:76px">
    <li><svg class="ico"><use href="#i-phone"/></svg>555-014-2731</li>
    <li><svg class="ico"><use href="#i-fax"/></svg>555-014-2736</li>
    <li class="gap"><svg class="ico"><use href="#i-mail"/></svg>daniel@brookvaleestates.us</li>
    <li><svg class="ico"><use href="#i-web"/></svg>www.brookvaleestates.us</li>
    <li class="addr">2180 Larkin Ave. #310</li>
    <li style="color:var(--brand-blue)">Fairview, CA 90000</li>
  </ul>
</section>

<section class="sheet card card-back" aria-label="Business card back">
  <div class="pattern-field" role="img" aria-label="Faint repeating brand pattern in light grey"></div>
  <div class="abs wordmark" style="right:18px;top:138px;font-size:12px;background:var(--paper);padding:3px 4px">
    <span class="dot" style="width:15px;height:15px"></span>BROOKVALE ESTATES
  </div>
</section>

<section class="sheet letterhead" aria-label="Letterhead">
  <div class="abs wordmark" style="left:51px;top:40px;font-size:12.5px">
    <span class="dot" style="width:18px;height:18px"></span>BROOKVALE ESTATES
  </div>
  <ul class="abs contact small lh-contact" style="left:336px;top:19px">
    <li><svg class="ico"><use href="#i-phone"/></svg>555-014-2731</li>
    <li><svg class="ico"><use href="#i-fax"/></svg>555-014-2736</li>
    <li style="margin-top:3px"><svg class="ico"><use href="#i-pin"/></svg>2180 Larkin Ave. #310</li>
    <li style="padding-left:11px">Fairview, CA 90000</li>
    <li style="margin-top:3px"><svg class="ico"><use href="#i-web"/></svg>www.brookvaleestates.us</li>
  </ul>
  <div class="abs deco-ring" style="left:287px;top:333px;width:300px;height:300px;border:14px solid var(--faint-grey)"></div>
</section>

<section class="sheet envelope env-front" aria-label="Envelope front">
  <div class="abs wordmark" style="left:20px;top:26px;font-size:9px">
    <span class="dot" style="width:14px;height:14px"></span>BROOKVALE ESTATES
  </div>
  <div class="abs" style="left:146px;top:24px;width:1px;height:17px;background:var(--brand-blue)"></div>
  <div class="abs" style="left:153px;top:26px;font-size:6.5px;line-height:8px;color:var(--charcoal);white-space:nowrap">
    2180 Larkin Ave. #310<br>Fairview, CA 90000
  </div>
</section>

<section class="sheet envelope env-back" aria-label="Envelope back">
  <svg class="flap" viewBox="0 0 550 84" aria-hidden="true">
    <path d="M0 0H550L542 80Q541 84 536 84H14Q9 84 8 80Z" fill="#fff" stroke="#d8d8d8" stroke-width="1"/>
    <path d="M10 84H540" stroke="#c9c9c9" stroke-width="2"/>
  </svg>
  <div class="abs deco-ring" style="left:255px;top:18px;width:42px;height:42px;background:var(--charcoal)"></div>
</section>

</body>
</html>
```